Business Cards - Brightpath Horizon

need to design unique business card for my mortgage business. I need to design credit card style business card for my business or any unique idea that you might have

Target Market(s)

Home Loan customers

Industry/Entity Type

Mortgage Brokerage

Contact Information for Business Card

please design credit card style or very unique style business card

Colors

Designer to choose colors to be used in the design.

Requirements
Must have
• Name
• position
• Phone number
• fax number
• email address
• website address
• social media address
• All above fields will be provided once design in finalised

```html
<!DOCTYPE html>
<html lang="en">
<head>
<meta charset="utf-8">
<title>Brightpath Horizon – Business Card</title>
<link href="https://fonts.googleapis.com/css2?family=Bodoni+Moda:wght@500&family=PT+Serif:wght@400&display=swap" rel="stylesheet">
<style>
  :root {
    --backdrop: #7a5a40;
    --card-white: #ffffff;
    --brand-blue: #0530c8;
    --brand-orange: #f7941d;
    --text-grey: #4a4a4a;
    --tree-tint: #2a55d6;
    --icon-blue: #1a3ec4;
  }
  * { margin: 0; padding: 0; box-sizing: border-box; }
  html, body {
    width: 1200px; height: 960px; overflow: hidden;
    background: var(--backdrop);
  }
  .stage { position: relative; width: 1200px; height: 960px; }

  .card {
    position: absolute; width: 600px; height: 343px; overflow: hidden;
    box-shadow: 0 3px 6px rgba(0,0,0,0.35);
  }
  .card--front { left: 314px; top: 113px; background: var(--card-white); }
  .card--back { left: 312px; top: 472px; background: var(--brand-blue); }

  .holder { position: absolute; left: 45px; top: 158px; }
  .holder__name {
    font-family: "PT Serif", serif; font-size: 21px; color: var(--brand-blue);
    letter-spacing: 0.2px; line-height: 1;
  }
  .holder__role {
    font-family: "PT Serif", serif; font-size: 15px; color: var(--brand-orange);
    margin-top: 8px; line-height: 1;
  }

  .brand {
    font-family: "Bodoni Moda", serif; font-weight: 500;
    line-height: 1.05; letter-spacing: 1px;
  }
  .brand--front {
    position: absolute; left: 334px; top: 92px; width: 230px;
    font-size: 27px; color: var(--brand-blue); text-align: center;
  }

  .contact { position: absolute; left: 348px; top: 228px; list-style: none; }
  .contact__item {
    display: flex; align-items: center; gap: 8px; height: 19.3px;
    font-family: "PT Serif", serif; font-size: 14px; color: var(--text-grey);
  }
  .contact__icon { width: 14px; height: 14px; fill: var(--icon-blue); }

  .social { position: absolute; left: 32px; top: 48px; display: flex; gap: 4px; }
  .social__dot { width: 26px; height: 26px; border-radius: 50%; background: var(--card-white); }

  .brand--back {
    position: absolute; left: 30px; top: 232px;
    font-size: 27px; color: var(--card-white);
  }
  .web {
    position: absolute; left: 31px; top: 306px;
    font-family: "PT Serif", serif; font-size: 13px; letter-spacing: 2px;
    color: var(--card-white);
  }
  .tree-art {
    position: absolute; left: 262px; top: 0; width: 338px; height: 343px;
    background: radial-gradient(ellipse at 55% 42%, var(--tree-tint) 0%, var(--tree-tint) 48%, rgba(42,85,214,0) 70%);
  }
</style>
</head>
<body>
<main class="stage">
  <section class="card card--front" aria-label="Card front">
    <div class="holder">
      <p class="holder__name">DANIEL REYES</p>
      <p class="holder__role">CEO/FOUNDER</p>
    </div>

    <p class="brand brand--front">BRIGHTPATH<br>HORIZON</p>

    <ul class="contact">
      <li class="contact__item">
        <svg class="contact__icon" viewBox="0 0 16 16" aria-hidden="true"><path d="M3 1l3 3-1.5 2a9 9 0 0 0 5.5 5.5L12 10l3 3-2 2C6 15 1 10 1 3z"/></svg>
        555 214 7630
      </li>
      <li class="contact__item">
        <svg class="contact__icon" viewBox="0 0 16 16" aria-hidden="true"><rect x="4" y="1" width="8" height="4"/><rect x="1" y="6" width="14" height="6" rx="1"/><rect x="4" y="10" width="8" height="5"/></svg>
        555 214 7631
      </li>
      <li class="contact__item">
        <svg class="contact__icon" viewBox="0 0 16 16" aria-hidden="true"><path d="M1 3h14v10H1z M2 4l6 5 6-5" fill="none" stroke="#1a3ec4" stroke-width="1.6"/></svg>
        daniel@brightpathhorizon.com
      </li>
      <li class="contact__item">
        <svg class="contact__icon" viewBox="0 0 16 16" aria-hidden="true"><circle cx="8" cy="8" r="7"/><path d="M1 8h14M8 1c3 3 3 11 0 14M8 1c-3 3-3 11 0 14" fill="none" stroke="#fff" stroke-width="1"/></svg>
        www.brightpathhorizon.com
      </li>
    </ul>
  </section>

  <section class="card card--back" aria-label="Card back">
    <div class="social" aria-label="Social media links">
      <span class="social__dot"></span>
      <span class="social__dot"></span>
      <span class="social__dot"></span>
      <span class="social__dot"></span>
    </div>

    <div class="tree-art" role="img" aria-label="Large faint silhouette of a leafy tree"></div>

    <p class="brand brand--back">BRIGHTPATH<br>HORIZON</p>
    <p class="web">www.brightpathhorizon.com</p>
  </section>
</main>
</body>
</html>
```